Business card design

I already have the logo design completed and am requiring business card design and layout utilising the logo. I require a front and back design.

We are an executive recruitment company so we are looking at full colour, high finish in a reasonably conservative structure.

Reason: will be provide ai template

Target Market(s)

Senior Management 35-60 age bracket

Industry/Entity Type

Business

Requirements
Must have
• Peter Welling
• Director
• 238 Morrow Tce, Kelvin Grove QLD 4059
• Ph: 07 3628 4190 Mob: 0418527306
• peter@voltinapartners.com.au
• www.voltinapartners.com.au
Nice to have
• Ideally full colour,
Should not have
• cheap looking

```html
<!DOCTYPE html>
<html lang="en">
<head>
<meta charset="utf-8">
<title>Voltina Partners – Business Card</title>
<link rel="stylesheet" href="https://fonts.googleapis.com/css2?family=Montserrat:wght@400;500;700&display=swap">
<style>
  :root {
    --page-bg: #e9eaec;
    --brand-blue: #1f5f99;
    --brand-blue-deep: #0d3f73;
    --brand-blue-light: #3a7ab5;
    --ink-navy: #1c4b7a;
    --ink-grey: #4a4f57;
    --card-white: #f6f7f8;
    --rule: #6b8fb3;
  }
  * { box-sizing: border-box; margin: 0; padding: 0; }
  html, body {
    width: 1200px; height: 1200px; overflow: hidden;
    background: var(--page-bg);
    font-family: "Montserrat", sans-serif;
  }
  .sheet {
    width: 1200px; height: 1200px;
    display: flex; flex-direction: column; align-items: center; justify-content: center;
    gap: 52px;
  }
  .card {
    width: 900px; height: 514px;
    position: relative;
    box-shadow: 0 10px 30px rgba(0,0,0,0.15);
  }
  .wordmark { display: flex; align-items: center; }
  .wordmark-square { flex: none; background: currentColor; }
  .wordmark-name { font-weight: 700; line-height: 1; white-space: nowrap; }
  .website { white-space: nowrap; font-weight: 500; }

  /* Front */
  .card-front {
    background: radial-gradient(ellipse at 42% 35%, var(--brand-blue-light) 0%, var(--brand-blue) 45%, var(--brand-blue-deep) 100%);
    color: #fff;
  }
  .card-front .wordmark {
    position: absolute; left: 0; right: 0; top: 190px;
    justify-content: center; gap: 18px;
  }
  .card-front .wordmark-square { width: 52px; height: 52px; }
  .card-front .wordmark-name { font-size: 50px; letter-spacing: 2px; }
  .card-front .website {
    position: absolute; left: 0; right: 0; top: 340px;
    text-align: center; font-size: 28px; letter-spacing: 4px;
  }

  /* Back */
  .card-back {
    background: var(--card-white);
    display: grid; grid-template-columns: 440px 1px 1fr;
  }
  .back-brand {
    padding: 170px 20px 0 50px;
    color: var(--ink-navy);
    overflow: hidden;
  }
  .back-brand .wordmark { gap: 12px; }
  .back-brand .wordmark-square { width: 30px; height: 30px; }
  .back-brand .wordmark-name { font-size: 26px; letter-spacing: 1px; }
  .back-brand .website {
    margin-top: 70px;
    font-size: 18px; letter-spacing: 2.5px;
  }
  .divider {
    background: var(--rule); margin: 100px 0 120px;
  }
  .back-details {
    padding: 175px 30px 0 40px;
    color: var(--ink-grey);
  }
  .person-name {
    font-weight: 700; font-size: 44px; letter-spacing: 3px; color: var(--ink-navy); line-height: 1;
  }
  .person-phone { margin-top: 12px; font-size: 15px; letter-spacing: 2px; }
  .person-email { margin-top: 6px; font-size: 15px; white-space: nowrap; }
  .postal { margin-top: 28px; font-size: 14px; line-height: 1.55; letter-spacing: 1px; text-transform: uppercase; }
</style>
</head>
<body>
<main class="sheet">
  <section class="card card-front" aria-label="Card front">
    <div class="wordmark">
      <span class="wordmark-square"></span>
      <span class="wordmark-name">VOLTINA PARTNERS</span>
    </div>
    <p class="website">www.voltinapartners.com.au</p>
  </section>

  <section class="card card-back" aria-label="Card back">
    <div class="back-brand">
      <div class="wordmark">
        <span class="wordmark-square"></span>
        <span class="wordmark-name">VOLTINA PARTNERS</span>
      </div>
      <p class="website">www.voltinapartners.com.au</p>
    </div>
    <div class="divider"></div>
    <div class="back-details">
      <p class="person-name">NAME</p>
      <p class="person-phone">XXXX XXX XXX</p>
      <p class="person-email">admin@voltinapartners.com.au</p>
      <p class="postal">PO Box XX<br>XXXX XXXX XXXX<br>XXXX XX</p>
    </div>
  </section>
</main>
</body>
</html>
```